Business Cards for a law firm

Business cards for our law firm. Use our silhoette logo and OAK PARTNERS - check our website (www.oakpartners.example)

Contact Information for Business Card

our silhouette logo, OAK PARTNERS, 800-555-0147, Dorian Pemberton, dorian@oakpartners.example

Requirements
Must have
• our silhouette logo, OAK PARTNERS, 800-555-0147, Dorian Pemberton, dorian@oakpartners.example

```html
<!DOCTYPE html>
<html lang="en">
<head>
<meta charset="utf-8">
<title>Oak Partners – Business Cards</title>
<link rel="stylesheet" href="https://fonts.googleapis.com/css2?family=Montserrat:wght@700&family=Roboto:wght@400;500&display=swap">
<style>
  :root {
    --backdrop: #17181b;
    --navy-deep: #0f1d4a;
    --navy: #13237a;
    --blue-mid: #1e3a9a;
    --blue-light: #4a6fc4;
    --edge: #3e64b8;
    --white: #ffffff;
  }
  * { box-sizing: border-box; margin: 0; padding: 0; }
  html, body {
    width: 1200px; height: 840px; overflow: hidden;
    background: var(--backdrop);
  }
  .stage {
    position: relative; width: 1200px; height: 840px;
    display: flex; flex-direction: column; align-items: center; justify-content: center; gap: 40px;
  }
  .card {
    position: relative; width: 620px; height: 354px;
    border-radius: 26px; overflow: hidden;
    border: 2px solid var(--edge);
    box-shadow: 0 18px 40px rgba(0,0,0,.55);
  }
  .wordmark {
    display: flex; align-items: center; gap: 14px;
    font-family: "Montserrat", sans-serif; font-weight: 700;
    color: var(--white); letter-spacing: .06em; white-space: nowrap;
  }
  .wordmark-square { width: 26px; height: 26px; background: var(--white); flex: none; }

  /* Front */
  .card-front .pattern-area {
    position: absolute; inset: 0;
    background: linear-gradient(110deg, var(--navy-deep) 0%, var(--navy) 45%, var(--blue-mid) 70%, var(--blue-light) 100%);
  }
  .card-front .wordmark {
    position: absolute; left: 50%; top: 50%; transform: translate(-50%, -50%);
    font-size: 40px;
  }

  /* Back */
  .card-back {
    background:
      radial-gradient(ellipse at 65% 35%, var(--navy) 0%, transparent 60%),
      linear-gradient(100deg, var(--navy-deep) 0%, #111f5e 50%, var(--navy) 100%);
  }
  .card-back .wordmark {
    position: absolute; left: 48px; top: 50%; transform: translateY(-50%);
    font-size: 26px; gap: 10px;
  }
  .card-back .wordmark-square { width: 20px; height: 20px; }
  .divider {
    position: absolute; left: 330px; top: 110px; width: 1px; height: 134px;
    background: var(--white); opacity: .85;
  }
  .contact {
    position: absolute; left: 350px; top: 104px;
    color: var(--white); font-family: "Roboto", sans-serif;
  }
  .contact-name {
    font-family: "Montserrat", sans-serif; font-weight: 700;
    font-size: 21px; letter-spacing: .05em; margin-bottom: 12px;
  }
  .contact-list { list-style: none; }
  .contact-item {
    display: flex; align-items: center; gap: 9px;
    font-size: 17px; line-height: 30px;
  }
  .contact-icon { width: 16px; height: 16px; flex: none; }
</style>
</head>
<body>
<main class="stage">
  <section class="card card-front" aria-label="Card front">
    <div class="pattern-area" role="img" aria-label="Repeating pattern of standing figure silhouettes in shades of blue"></div>
    <div class="wordmark"><span class="wordmark-square"></span>OAK PARTNERS</div>
  </section>

  <section class="card card-back" aria-label="Card back">
    <div class="wordmark"><span class="wordmark-square"></span>OAK PARTNERS</div>
    <div class="divider"></div>
    <div class="contact">
      <p class="contact-name">DORIAN PEMBERTON</p>
      <ul class="contact-list">
        <li class="contact-item">
          <svg class="contact-icon" viewBox="0 0 16 16" aria-hidden="true"><path fill="#fff" d="M2 6c0-2 2.5-3 6-3s6 1 6 3l-2.5.8-.5-1.6H5L4.5 6.8zM4 8h8l1.5 5h-11z"/></svg>
          800-555-0147
        </li>
        <li class="contact-item">
          <svg class="contact-icon" viewBox="0 0 16 16" aria-hidden="true"><rect x="1" y="3.5" width="14" height="9.5" rx="1" fill="#fff"/><path d="M1.5 4l6.5 5 6.5-5" fill="none" stroke="#13237a" stroke-width="1.3"/></svg>
          dorian@oakpartners.example
        </li>
        <li class="contact-item">
          <svg class="contact-icon" viewBox="0 0 16 16" aria-hidden="true"><circle cx="8" cy="8" r="7" fill="#fff"/><g fill="none" stroke="#13237a" stroke-width="1"><ellipse cx="8" cy="8" rx="3" ry="7"/><path d="M1 8h14M2.5 4.5h11M2.5 11.5h11"/></g></svg>
          www.oakpartners.example
        </li>
      </ul>
    </div>
  </section>
</main>
</body>
</html>
```